Brightway Haus Inc. Business Card Design

Brightway Haus Inc. is in search of a great clean design for our business cards!

Looking to incorporate our full logo and watermark on side one (however, I am open to having the text and watermark separated within the design.)

On side two, I am looking to have contact information (Name, Position, Phone #, Email, Website (www.thebrightwayhaus.ca). Can have the logo and/or watermark as part of the design if applicable.

Please add tagline "Where Shine Counts" on either side 1 or 2. This tagline can be in a sans serif, serif or cursive font as long as it compliments overall design. Capitalization can be title or sentence case depending on how it fits within the design.

Get creative!! Looking for a clean, crisp, premium design! Looking for a glossy card finish with spot UV features when printed. Cards will also be printed with rounded corners. Standard dimensions (3.5 x 2).

Target Market(s)

B2B - primary clients are business owners or property management corporations. (residential jobs are few and far between)

Industry/Entity Type

Business

Contact Information for Business Card

- clean, crisp design
- double sided
- spot UV accents and glossy finish upon printing
- standard business card size (3.5 x 2) with rounded corners
- please see project description for requirements per side

Font styles to use
Sans Serif

Requirements
Must have
• - adequate bleeds with print ready files
• - cohesive design elements between side 1 & 2
• - spot UV elements (can be on both sides or just one, use your discretion)
• - colour pallet should match the logo file provided
• - incorporate tagline "where shine counts" (this tagline can be in a serif or sans serif font as long as it is complimentary to the overall design.
Nice to have
• - Premium elements with a clean design
Should not have
• - Please omit cartoon or whimsical like designs, think premium.
• - Colours should not stray from the pallet of the provided logo.

```html
<!DOCTYPE html>
<html lang="en">
<head>
<meta charset="utf-8">
<title>Brightway Haus Inc. Business Cards</title>
<link rel="stylesheet" href="https://fonts.googleapis.com/css2?family=Source+Sans+3:wght@400;600;700&display=swap">
<style>
  :root {
    --bg: #d9dadc;
    --white: #ffffff;
    --teal: #10b8b8;
    --navy: #1b2350;
    --silver: #c9cbce;
    --shadow: rgba(0, 0, 0, 0.35);
  }
  * { box-sizing: border-box; margin: 0; padding: 0; }
  html, body {
    width: 1200px; height: 960px; overflow: hidden;
    background: var(--bg);
    font-family: "Source Sans 3", "Segoe UI", sans-serif;
  }
  .stage { position: relative; width: 1200px; height: 960px; }
  .card {
    position: absolute; width: 600px; height: 344px;
    border-radius: 22px; overflow: hidden;
    box-shadow: 0 4px 8px var(--shadow);
  }
  .card-front { left: 314px; top: 113px; background: var(--white); }
  .card-back { left: 311px; top: 472px; height: 342px; background: var(--navy); }
  .swoosh { position: absolute; inset: 0; width: 600px; height: 344px; }

  .brand { position: absolute; display: flex; align-items: center; gap: 10px; }
  .brand-mark { width: 30px; height: 30px; background: var(--navy); }
  .brand-name {
    font-weight: 700; font-size: 30px; letter-spacing: -0.3px;
    line-height: 1; white-space: nowrap;
  }
  .card-front .brand { left: 38px; top: 78px; }
  .card-front .brand-name { color: var(--teal); }
  .card-back .brand { left: 0; right: 0; top: 150px; justify-content: center; }
  .card-back .brand-name { color: var(--silver); font-size: 36px; }
  .card-back .brand-mark { width: 36px; height: 36px; background: var(--silver); }

  .contact {
    position: absolute; right: 22px; top: 136px;
    color: var(--white); text-align: right; font-size: 14.5px; line-height: 19.3px;
  }
  .contact-name { font-weight: 700; font-size: 16px; line-height: 20px; }
  .contact-role { font-size: 16px; line-height: 22px; margin-bottom: 5px; }
  .contact-address { margin-bottom: 5px; }
  .contact-line { display: flex; justify-content: flex-end; align-items: center; gap: 7px; }
  .contact-line svg { width: 13px; height: 13px; fill: var(--white); flex: none; }

  .tagline {
    position: absolute; left: 0; right: 0; top: 276px;
    display: flex; justify-content: center; align-items: center; gap: 4px;
    color: var(--white); font-weight: 600; font-size: 18px;
  }
  .tagline-rule { width: 112px; height: 1px; }
  .tagline-rule.left { background: linear-gradient(to right, transparent, var(--white)); }
  .tagline-rule.right { background: linear-gradient(to left, transparent, var(--white)); }
</style>
</head>
<body>
<main class="stage">
  <section class="card card-front" aria-label="Business card front">
    <svg class="swoosh" viewBox="0 0 600 344" aria-hidden="true">
      <path fill="var(--navy)" d="M0,306 C55,330 140,322 238,280 C350,196 468,98 566,0 L600,0 L600,344 L0,344 Z"/>
      <path fill="var(--teal)" stroke="var(--white)" stroke-width="2" d="M0,318 C60,338 150,330 250,290 C360,205 480,110 600,10 L600,344 L0,344 Z"/>
    </svg>
    <div class="brand">
      <span class="brand-mark"></span>
      <span class="brand-name">BRIGHTWAY HAUS INC.</span>
    </div>
    <div class="contact">
      <p class="contact-name">MARCUS DELANY</p>
      <p class="contact-role">CEO/FOUNDER</p>
      <p class="contact-address">214 Harbourview Road<br>Halifax, NS B3H 2Y9</p>
      <p class="contact-line">902 555 0148
        <svg viewBox="0 0 16 16"><path d="M1 6c0-3 14-3 14 0v2h-4V6H5v2H1zM4 9h8l2 5H2z"/></svg></p>
      <p class="contact-line">902 555 0273
        <svg viewBox="0 0 16 16"><path d="M4 0h8v16H4zM5.5 2v10h5V2z"/></svg></p>
      <p class="contact-line">902 555 0391
        <svg viewBox="0 0 16 16"><path d="M4 1h8v4H4zM1 6h14v7H1zM4 10h8v5H4z"/></svg></p>
      <p class="contact-line">hello@brightwayhaus.ca
        <svg viewBox="0 0 16 16"><path d="M1 3h14v1L8 9 1 4zM1 6l7 5 7-5v7H1z"/></svg></p>
      <p class="contact-line">www.thebrightwayhaus.ca
        <svg viewBox="0 0 16 16"><circle cx="8" cy="8" r="7"/></svg></p>
    </div>
  </section>

  <section class="card card-back" aria-label="Business card back">
    <div class="brand">
      <span class="brand-mark"></span>
      <span class="brand-name">BRIGHTWAY HAUS INC.</span>
    </div>
    <p class="tagline">
      <span class="tagline-rule left"></span>Where Shine Counts<span class="tagline-rule right"></span>
    </p>
  </section>
</main>
</body>
</html>
```